I am looking for a modern, clean and neat design for a reflexology and well being business. The business name is Gralo Tund (this is an old Latin word for wellbeing). The colours I would like are purple, white and grey. I am open to suggestions for pictures such as healing or working hands, a pair of feet, images that represent my business that you may think of....... or maybe you think no images at all would be best? My tag line is: "Relax, Renew, Revive" or "Find you balance......... Relax, Renew, Revive" I can decide which I want so I would like to see what both would look like. I would like space on the back to write the client's appointment date and time (more than once)

```html
<!DOCTYPE html>
<html lang="en">
<head>
<meta charset="utf-8">
<title>Gralo Tund – Business Card</title>
<link rel="stylesheet" href="https://fonts.googleapis.com/css2?family=Exo+2:wght@400&family=Open+Sans:wght@400;600;700&display=swap">
<style>
  :root {
    --page: #2b2b2b;
    --card-black: #050505;
    --lavender: #9fb3de;
    --mid-grey: #555555;
    --white: #ffffff;
    --ink-grey: #3a3a3a;
  }
  * { box-sizing: border-box; margin: 0; padding: 0; }
  html, body { width: 1200px; height: 900px; overflow: hidden; }
  body {
    background: var(--page);
    position: relative;
    font-family: "Open Sans", Arial, sans-serif;
  }
  .card {
    position: absolute;
    width: 560px;
    height: 320px;
    border-radius: 28px;
    background: var(--card-black);
    overflow: hidden;
    box-shadow: 0 14px 30px rgba(0,0,0,.45);
  }
  .card--back { left: 90px; top: 110px; }
  .card--front { left: 550px; top: 470px; }

  /* back */
  .brand-top {
    position: absolute; right: 40px; top: 34px;
    text-align: right; color: var(--white);
  }
  .brand-top .brand-name {
    display: flex; align-items: center; justify-content: flex-end; gap: 12px;
    font-family: "Exo 2", sans-serif; font-size: 30px; letter-spacing: 2px;
  }
  .brand-dot { width: 22px; height: 22px; border-radius: 50%; background: var(--lavender); }
  .tagline {
    margin-top: 10px; font-size: 12px; font-weight: 600; letter-spacing: 1px;
  }
  .appointment {
    position: absolute; left: 40px; bottom: 36px; width: 380px; color: var(--white);
  }
  .appointment h2 { font-size: 18px; font-weight: 700; margin-bottom: 10px; }
  .appointment .field {
    display: flex; align-items: flex-end; gap: 4px;
    font-size: 13px; margin: 0 0 10px 22px;
  }
  .appointment .field .line {
    flex: 1; border-bottom: 2px dotted rgba(255,255,255,.85); height: 1px; margin-bottom: 4px;
  }

  /* front */
  .front-shapes { position: absolute; inset: 0; }
  .brand-main {
    position: absolute; left: 46px; top: 112px;
    display: flex; align-items: center; gap: 16px;
    font-family: "Exo 2", sans-serif; font-size: 38px; letter-spacing: 3px; color: var(--white);
  }
  .brand-main .brand-dot { width: 34px; height: 34px; }
  .contact {
    position: absolute; left: 380px; top: 168px; color: var(--lavender);
  }
  .contact .person-name { font-size: 21px; font-weight: 700; letter-spacing: 1px; }
  .contact .role { font-size: 11px; font-weight: 600; color: var(--ink-grey); margin-bottom: 10px; }
  .contact li {
    list-style: none; display: flex; align-items: center; gap: 8px;
    font-size: 12px; line-height: 17px;
  }
  .contact svg { width: 10px; height: 10px; fill: var(--ink-grey); flex: none; }
</style>
</head>
<body>

<section class="card card--back" aria-label="Card back">
  <div class="brand-top">
    <div class="brand-name"><span class="brand-dot"></span>GRALO TUND</div>
    <p class="tagline">RELAX, RENEW, REVIVE</p>
  </div>
  <div class="appointment">
    <h2>Appointment:</h2>
    <div class="field"><span>Name:</span><span class="line"></span></div>
    <div class="field"><span>Time:</span><span class="line"></span></div>
    <div class="field"><span>Date:</span><span class="line"></span></div>
  </div>
</section>

<section class="card card--front" aria-label="Card front">
  <svg class="front-shapes" viewBox="0 0 560 320" width="560" height="320" aria-hidden="true">
    <path fill="var(--mid-grey)" d="M330 320 C270 280 240 210 262 150 C285 90 350 60 405 78 C420 84 432 92 440 100 C452 80 475 62 505 55 C530 50 550 52 560 56 L560 320 Z"/>
    <path fill="var(--white)" d="M400 320 C365 290 345 245 352 205 C360 160 400 138 445 150 C456 153 466 160 472 168 C482 152 500 140 525 136 C540 134 552 136 560 140 L560 320 Z"/>
  </svg>
  <div class="brand-main"><span class="brand-dot"></span>GRALO TUND</div>
  <div class="contact">
    <p class="person-name">MARA QUELL</p>
    <p class="role">DIRECTOR</p>
    <ul>
      <li><svg viewBox="0 0 10 10"><path d="M2 0.5 L3.8 2.6 L2.9 3.6 C3.5 5 5 6.5 6.4 7.1 L7.4 6.2 L9.5 8 L8.3 9.5 C4.5 9.2 0.8 5.5 0.5 1.7 Z"/></svg>+330 5550-1274</li>
      <li><svg viewBox="0 0 10 10"><path d="M0.5 2 H9.5 V8 H0.5 Z M1.5 3 L5 5.6 L8.5 3 V7 H1.5 Z" fill-rule="evenodd"/></svg>info@gralotund.com</li>
      <li><svg viewBox="0 0 10 10"><circle cx="5" cy="5" r="4.5"/></svg>www.gralotund.com</li>
    </ul>
  </div>
</section>

</body>
</html>
```